buisnes card for Gentle Tide Reflexology

I need a new business card with my information
Hedwig Brommelsiek
MPLVA,KTZQ,RN(Grermany)
Cranio-Sacral Reflexology
Facial Reflexology, Veldmarkmethod TM
Nerve point Reflexology
41576 Marrowfield Road
Abbotsford,BC
Gentletidereflexology.ca
I would like the design to show that I work mostly with clients that have health problems.(80% are back/spine related problems).
I would like the card to be professional as well as inviting. I like nature aspects as well.
I have two websites that I like so you have an Idea what kind of design speaks to me.
1. www.pondorava.ca the art of healing (Chilliwack)
2.www.quietharbourdoula.ca (Abbotsford)

My treatment room is blue and the outside of our house is dark blue and grey. That are colors that could be incorporated

Target Market(s)

clients that are looking for a more natural approach to their health issues

Industry/Entity Type

Health And Wellness

Contact Information for Business Card

Hedwig Brommelsiek
MPLVA,KTZQ,RN(Grermany)
Cranio-Sacral Reflexology
Nerve point Reflexology
41576 Marrowfield Road
Abbotsford,BC
Gentletidereflexology.ca

Colors
0355a3
0492cd

Requirements
Must have
• name, address, phonenumber
Nice to have
• 1. www.pondorava.ca the art of healing (Chilliwack)
• 2.www.quietharbourdoula.ca (Abbotsford)
• This are designs that I like.

```html
<!DOCTYPE html>
<html lang="en">
<head>
<meta charset="utf-8">
<title>Gentle Tide Reflexology – Business Card</title>
<link href="https://fonts.googleapis.com/css2?family=Arimo:wght@400;700&display=swap" rel="stylesheet">
<style>
  :root {
    --page-bg: #e9ecef;
    --card-deep: #0355a3;
    --card-mid: #0a6fc0;
    --card-light: #2f8fd6;
    --text-main: #ffffff;
    --text-soft: #dbeaf7;
    --figure-blue: #3d6fd8;
    --figure-glow: #b04fd0;
    --spine-glow: #e0623a;
  }
  * { box-sizing: border-box; margin: 0; padding: 0; }
  html, body { width: 1200px; height: 780px; overflow: hidden; }
  body {
    background: var(--page-bg);
    font-family: "Arimo", Arial, sans-serif;
    color: var(--text-main);
    display: flex;
    align-items: center;
    justify-content: center;
    gap: 40px;
  }
  .card {
    position: relative;
    width: 560px;
    height: 320px;
    border-radius: 16px;
    overflow: hidden;
    background: radial-gradient(ellipse at 55% 55%, var(--card-light) 0%, var(--card-mid) 45%, var(--card-deep) 100%);
    box-shadow: 0 6px 18px rgba(0, 40, 90, 0.25);
  }
  /* Front */
  .front .figure-art {
    position: absolute;
    left: 20px; top: 40px;
    width: 240px; height: 260px;
    border-radius: 40%;
    background: radial-gradient(ellipse at 55% 50%, var(--figure-glow) 0%, var(--figure-blue) 40%, rgba(61,111,216,0) 72%);
    opacity: 0.85;
  }
  .front .details {
    position: absolute;
    left: 262px; top: 30px;
    right: 20px;
  }
  .name {
    font-weight: 700;
    font-size: 24px;
    letter-spacing: -0.2px;
    line-height: 1.1;
  }
  .credentials {
    font-size: 12px;
    color: var(--text-soft);
    margin-top: 3px;
  }
  .services {
    margin-top: 12px;
    font-size: 13px;
    line-height: 1.35;
  }
  .contact-list {
    list-style: none;
    margin-top: 12px;
    font-size: 13px;
    line-height: 1.5;
  }
  .contact-list li { display: flex; align-items: center; gap: 8px; }
  .contact-icon {
    width: 13px; height: 13px;
    flex: none;
  }
  .address {
    margin-top: 12px;
    font-size: 15px;
    line-height: 1.35;
  }
  /* Back */
  .back .identity {
    position: absolute;
    left: 30px; top: 32px;
  }
  .back .name { font-size: 24px; }
  .back .site {
    font-size: 14px;
    font-weight: 700;
    margin-top: 6px;
  }
  .back .spine-art {
    position: absolute;
    right: -20px; bottom: -20px;
    width: 380px; height: 210px;
    border-radius: 50%;
    background: radial-gradient(ellipse at 60% 55%, var(--spine-glow) 0%, var(--figure-blue) 38%, rgba(61,111,216,0) 72%);
    opacity: 0.85;
  }
</style>
</head>
<body>

  <section class="card front" aria-label="Business card front">
    <div class="figure-art" role="img" aria-label="Translucent anatomical figure of a seated person holding a glowing knee, skeleton visible"></div>
    <div class="details">
      <h1 class="name">Hedwig Brommelsiek</h1>
      <p class="credentials">MPLVA,KTZQ,RN(Grermany)</p>
      <p class="services">
        Cranio-Sacral Reflexology<br>
        Facial Reflexology, Veldmarkmethod TM<br>
        Nerve point Reflexology
      </p>
      <ul class="contact-list">
        <li>
          <svg class="contact-icon" viewBox="0 0 14 14" aria-hidden="true">
            <rect width="14" height="14" rx="2" fill="#fff"/>
            <path d="M4 3h2l1 2.5-1.2 1a6 6 0 0 0 2.7 2.7l1-1.2L12 9v2a1 1 0 0 1-1 1A8 8 0 0 1 3 4a1 1 0 0 1 1-1z" fill="#0355a3"/>
          </svg>
          000.000.0000
        </li>
        <li>
          <svg class="contact-icon" viewBox="0 0 14 14" aria-hidden="true">
            <rect width="14" height="14" rx="2" fill="#fff"/>
            <circle cx="7" cy="7" r="4.2" fill="none" stroke="#0355a3" stroke-width="1.2"/>
            <path d="M2.8 7h8.4M7 2.8c-2 2.4-2 6 0 8.4M7 2.8c2 2.4 2 6 0 8.4" fill="none" stroke="#0355a3" stroke-width="1"/>
          </svg>
          Gentletidereflexology.ca
        </li>
        <li>
          <svg class="contact-icon" viewBox="0 0 14 14" aria-hidden="true">
            <rect width="14" height="14" rx="2" fill="#fff"/>
            <rect x="2.5" y="4" width="9" height="6.5" fill="none" stroke="#0355a3" stroke-width="1.2"/>
            <path d="M2.5 4l4.5 3.6L11.5 4" fill="none" stroke="#0355a3" stroke-width="1.2"/>
          </svg>
          hello@tidemailbox.ca
        </li>
      </ul>
      <p class="address">
        41576 Marrowfield Road<br>
        Abbotsford,BC
      </p>
    </div>
  </section>

  <section class="card back" aria-label="Business card back">
    <div class="identity">
      <h2 class="name">Hedwig Brommelsiek</h2>
      <p class="credentials">MPLVA,KTZQ,RN(Grermany)</p>
      <p class="site">Gentletidereflexology.ca</p>
    </div>
    <div class="spine-art" role="img" aria-label="Translucent reclining figure with a glowing red spine and highlighted neck and lower back"></div>
  </section>

</body>
</html>
```